TalkHarbor - Language Coaching Services

Sleek, innovative, trendy design for Language Coaching business.

TalkHarbor is a new UK based company that provides Language Coaching services. We offer highly personalized on-line and face to face language courses. We also impart learning techniques workshops based on the latest neuroscience research for second-language acquisition.

Target Market(s)

See attached info

Industry/Entity Type

Consulting

Contact Information for Business Card

TalkHarbor
DaniaKV@talkharbor.co.uk
TalkHarbor.co.uk
London, UK

Font styles to use
Sans Serif

```html
<!DOCTYPE html>
<html lang="en">
<head>
<meta charset="utf-8">
<title>TalkHarbor Business Card</title>
<link rel="stylesheet" href="https://fonts.googleapis.com/css2?family=Lato:wght@400;700&family=Montserrat:wght@600&display=swap">
<style>
  :root {
    --backdrop: #e3e3e5;
    --brand-blue: #0a8fcf;
    --brand-blue-deep: #066fa3;
    --brand-blue-light: #1fb0e6;
    --ink: #3c3c3c;
    --paper: #ffffff;
    --ring-faint: #e3f1f8;
  }
  * { margin: 0; padding: 0; box-sizing: border-box; }
  html, body { width: 1200px; height: 900px; overflow: hidden; }
  body {
    background: var(--backdrop);
    font-family: "Lato", Arial, sans-serif;
    position: relative;
  }
  .card {
    position: absolute;
    width: 500px;
    height: 286px;
    border-radius: 22px;
    overflow: hidden;
    box-shadow: 0 6px 18px rgba(0,0,0,0.18);
  }
  .card-front {
    left: 90px; top: 150px;
    background: linear-gradient(180deg, var(--brand-blue-deep) 0%, var(--brand-blue-light) 55%, var(--brand-blue) 100%);
    display: flex; flex-direction: column; align-items: center; justify-content: center;
    gap: 18px;
  }
  .brand-mark {
    display: flex; align-items: center; gap: 14px;
  }
  .brand-dot {
    border-radius: 50%;
    flex: none;
  }
  .card-front .brand-dot { width: 54px; height: 54px; border: 5px solid var(--paper); }
  .brand-name {
    font-family: "Montserrat", Arial, sans-serif;
    font-weight: 600;
    letter-spacing: 3px;
    text-transform: uppercase;
  }
  .card-front .brand-name { color: var(--paper); font-size: 34px; }

  .card-back {
    left: 610px; top: 460px;
    background: var(--paper);
  }
  .back-ring {
    position: absolute; right: -70px; top: -60px;
    width: 260px; height: 260px;
    border: 22px solid var(--ring-faint);
    border-radius: 50%;
  }
  .card-back .brand-mark { position: absolute; left: 34px; top: 56px; }
  .card-back .brand-dot { width: 62px; height: 62px; border: 6px solid var(--brand-blue); }
  .card-back .brand-name { color: var(--brand-blue); font-size: 28px; }
  .person { position: absolute; left: 40px; top: 150px; }
  .person-name {
    font-size: 17px; letter-spacing: 1px; text-transform: uppercase;
    color: var(--brand-blue); font-weight: 700;
  }
  .person-role { font-size: 14px; color: var(--ink); margin-top: 1px; }
  .contacts { list-style: none; margin-top: 10px; }
  .contacts li {
    display: flex; align-items: center; gap: 8px;
    font-size: 14px; color: var(--ink); line-height: 20px;
  }
  .contacts svg { width: 13px; height: 13px; flex: none; }
  .office {
    position: absolute; right: 30px; top: 120px; text-align: right;
  }
  .office-name { font-size: 14px; font-weight: 700; color: var(--brand-blue); letter-spacing: 0.5px; }
  .office-city { font-size: 14px; color: var(--ink); }
</style>
</head>
<body>
  <section class="card card-front">
    <div class="brand-mark">
      <span class="brand-dot"></span>
      <span class="brand-name">TalkHarbor</span>
    </div>
  </section>

  <section class="card card-back">
    <div class="back-ring"></div>
    <div class="brand-mark">
      <span class="brand-dot"></span>
      <span class="brand-name">TalkHarbor</span>
    </div>
    <div class="office">
      <p class="office-name">TALKHARBOR</p>
      <p class="office-city">London, UK</p>
    </div>
    <div class="person">
      <p class="person-name">Oliver Brandt</p>
      <p class="person-role">Managing Director</p>
      <ul class="contacts">
        <li>
          <svg viewBox="0 0 14 14" aria-hidden="true"><rect x="3" y="1" width="8" height="12" rx="1.5" fill="none" stroke="#0a8fcf" stroke-width="1.6"/><circle cx="7" cy="10.5" r="0.9" fill="#0a8fcf"/></svg>
          044 777 1234
        </li>
        <li>
          <svg viewBox="0 0 14 14" aria-hidden="true"><rect x="1" y="3" width="12" height="8" rx="1" fill="#0a8fcf"/><path d="M1.5 3.5 L7 8 L12.5 3.5" fill="none" stroke="#fff" stroke-width="1.1"/></svg>
          DaniaKV@talkharbor.co.uk
        </li>
        <li>
          <svg viewBox="0 0 14 14" aria-hidden="true"><circle cx="7" cy="7" r="6" fill="#0a8fcf"/><path d="M1 7 H13 M7 1 C4 4 4 10 7 13 M7 1 C10 4 10 10 7 13" fill="none" stroke="#fff" stroke-width="0.9"/></svg>
          www.TalkHarbor.co.uk
        </li>
      </ul>
    </div>
  </section>
</body>
</html>
```